Business Card Design Project

I require a business card with the following information on them for various different people;
name
m:
f:
e:
I have a logo already and will attached that. We are in the construction industry. I require something clean and simple but eye catching at the same time. You can use another colour with our logo if you like and you can style the logo as well if you wish. I am open.
Also it needs to be front and back design.
Industry/Entity Type
Construction
Requirements
Must have
- Logo, name, mobile, fax and email address.
Front and back design

```html
<!DOCTYPE html>
<html lang="en">
<head>
<meta charset="utf-8">
<title>Verdant Ridge Builders – Business Cards</title>
<link href="https://fonts.googleapis.com/css2?family=Questrial&family=Open+Sans:wght@400;600&display=swap" rel="stylesheet">
<style>
  :root {
    --stage: #1c1c1c;
    --card: #ffffff;
    --green: #4fae3a;
    --green-dark: #3c9a2c;
    --ink: #2b2b2b;
    --grey: #6a6a6a;
    --black: #111111;
  }
  html, body {
    margin: 0;
    padding: 0;
    width: 1200px;
    height: 944px;
    overflow: hidden;
    background: var(--stage);
  }
  .stage {
    position: relative;
    width: 1200px;
    height: 944px;
  }
  .card {
    position: absolute;
    width: 680px;
    height: 390px;
    background: var(--card);
    border-radius: 26px;
    overflow: hidden;
    box-shadow: 0 10px 28px rgba(0,0,0,0.45);
  }
  .card--front { left: 90px; top: 60px; }
  .card--back { left: 430px; top: 494px; }

  .brand {
    display: flex;
    align-items: center;
    gap: 16px;
    font-family: "Questrial", sans-serif;
    color: var(--green);
    white-space: nowrap;
  }
  .brand__square {
    background: var(--green);
    flex: none;
  }
  .card--front .brand {
    position: absolute;
    left: 0; right: 0;
    top: 130px;
    justify-content: center;
    font-size: 52px;
  }
  .card--front .brand__square { width: 52px; height: 52px; }
  .front__web {
    position: absolute;
    left: 0; right: 0;
    top: 262px;
    text-align: center;
    font-family: "Open Sans", sans-serif;
    font-size: 21px;
    letter-spacing: 1.5px;
    color: var(--ink);
  }

  .back__swoosh {
    position: absolute;
    inset: 0;
    width: 680px;
    height: 390px;
  }
  .card--back .brand {
    position: absolute;
    left: 40px;
    top: 78px;
    font-size: 32px;
    gap: 12px;
  }
  .card--back .brand__square { width: 32px; height: 32px; }
  .contacts {
    position: absolute;
    left: 44px;
    top: 220px;
    margin: 0;
    padding: 0;
    list-style: none;
    font-family: "Open Sans", sans-serif;
    font-size: 19px;
    color: var(--ink);
  }
  .contacts li {
    display: flex;
    align-items: center;
    gap: 12px;
    height: 28px;
  }
  .contacts svg { width: 16px; height: 16px; flex: none; }
  .person {
    position: absolute;
    left: 470px;
    width: 190px;
    top: 200px;
    text-align: center;
    font-family: "Open Sans", sans-serif;
    color: #ffffff;
  }
  .person__name { font-size: 24px; margin: 0; font-weight: 400; }
  .person__role { font-size: 16px; margin: 4px 0 0; }
</style>
</head>
<body>
<main class="stage">

  <section class="card card--front" aria-label="Card front">
    <div class="brand">
      <span class="brand__square"></span>
      <span class="brand__name">Verdant Ridge Builders</span>
    </div>
    <p class="front__web">www.verdantridge.com</p>
  </section>

  <section class="card card--back" aria-label="Card back">
    <svg class="back__swoosh" viewBox="0 0 680 390" aria-hidden="true">
      <path d="M430 0 C 470 120 470 270 410 390 L680 390 L680 0 Z" fill="var(--black)"/>
      <path d="M446 0 C 492 120 490 270 432 390 L680 390 L680 0 Z" fill="var(--green)"/>
    </svg>

    <div class="brand">
      <span class="brand__square"></span>
      <span class="brand__name">Verdant Ridge Builders</span>
    </div>

    <ul class="contacts">
      <li>
        <svg viewBox="0 0 16 16" aria-hidden="true"><path d="M4 1 L7 4 L5.5 6 C6.5 8 8 9.5 10 10.5 L12 9 L15 12 L13 15 C7 15 1 9 1 3 Z" fill="var(--green)"/></svg>
        512-555-0140
      </li>
      <li>
        <svg viewBox="0 0 16 16" aria-hidden="true"><rect x="4" y="1" width="8" height="5" fill="var(--green)"/><rect x="1" y="7" width="14" height="8" rx="1.5" fill="var(--green)"/></svg>
        512-555-0141
      </li>
      <li>
        <svg viewBox="0 0 16 16" aria-hidden="true"><rect x="1" y="3" width="14" height="10" rx="1.5" fill="var(--green)"/><path d="M1.5 4 L8 9 L14.5 4" stroke="#fff" stroke-width="1.4" fill="none"/></svg>
        info@verdantridge.com
      </li>
      <li>
        <svg viewBox="0 0 16 16" aria-hidden="true"><circle cx="8" cy="8" r="7" fill="var(--green)"/></svg>
        www.verdantridge.com
      </li>
    </ul>

    <div class="person">
      <p class="person__name">Marcus Ellery</p>
      <p class="person__role">director</p>
    </div>
  </section>

</main>
</body>
</html>
```